Professional Website for Leading Global Private Equity Real Estate Company

The company is a leading global Private Equity Real Estate (PERE). We need a homepage design, an inner page design, and color/font tweaks to the logo (color should be more soothing than current blue used in the logo). The logo website should project the company as global, professional, experienced, trustworthy, accessible, YOUNG, DYNAMIC, hi-tech. PLEASE SEE the attached Design Brief Word Doc for details.

Target Market(s)

institional investors and wealthy private individuals

Industry/Entity Type

Finance

Number of Pages Required

2 page

Font styles to use
Sans Serif
Other font styles liked:
• either like in https://www.ferndalequay.com/ or like in presentations (Montserrat Black & Montserrat Light, Century Gothic, Blair ITC, Almoni Neue DL 4.0 AAA Medium, Almoni DL AAA)

Requirements
Must have
• new color palette that is NOT based on current logo. they want a more soothing color palette than the blue in that logo. the new color palette should project: global, professional, experienced, trustworthy, accessible, YOUNG, DYNAMIC, hi-tech.
Nice to have
• the likes these sites: https://www.ferndalequay.com/ and https://www.tvr.law/

```html
<!DOCTYPE html>
<html lang="en">
<head>
<meta charset="utf-8">
<title>Veridia Real Estate — Homepage Concepts</title>
<link rel="stylesheet" href="https://fonts.googleapis.com/css2?family=Lexend+Giga:wght@400;500&family=Montserrat:wght@400;500;600&display=swap">
<style>
:root{
  --board:#d3d3d5;
  --ink:#262a30;
  --muted:#5d6168;
  --white:#ffffff;
  --navy:#13306e;
  --royal:#1d47a8;
  --deep-blue:#0b2f86;
  --sky:#cfdcf4;
  --teal:#2f9d72;
  --teal-dark:#22825c;
  --forest:#2f7a34;
  --forest-dark:#1f5e22;
  --leaf:#7fae6a;
  --mint:#d8eadb;
  --mist:#efeff1;
  --footer:#eef0f3;
}
*{box-sizing:border-box;margin:0;padding:0}
html,body{width:1200px;height:1200px;overflow:hidden}
body{background:var(--board);font-family:'Montserrat',sans-serif;color:var(--ink);position:relative}
.page{position:absolute;overflow:hidden;background:var(--white)}
.sec{position:relative;overflow:hidden}
.abs{position:absolute}
.center-x{left:0;right:0;text-align:center}
.heading{font-family:'Lexend Giga',sans-serif;font-weight:400;letter-spacing:.04em;line-height:1.15;text-transform:uppercase}
.eyebrow{font-size:3px;letter-spacing:.18em;text-transform:uppercase;font-weight:500}
.copy{font-size:3.3px;line-height:1.75;color:var(--muted)}
.copy p+p{margin-top:3px}
.rule{height:1px;width:12px;background:var(--ink)}
.btn{display:flex;align-items:center;justify-content:center;font-size:2.8px;font-weight:600;letter-spacing:.1em;text-transform:uppercase}
.btn-outline{border:.8px solid currentColor}
.field{background:var(--white);font-size:2.6px;color:#777;padding-left:4px;display:flex;align-items:center}
.stat-num{font-family:'Lexend Giga',sans-serif;font-size:8.5px}
.stat-label{font-size:2.9px;text-transform:uppercase;letter-spacing:.03em}
.photo{position:absolute}
/* nav */
.nav{position:absolute;left:0;right:0;display:flex;align-items:center;color:var(--white)}
.brand{display:flex;align-items:center;gap:3px;font-size:5px;font-weight:600;letter-spacing:.06em;line-height:1}
.brand-dot{width:12px;height:12px;border-radius:50%;background:var(--white)}
.nav-links{display:flex;gap:8px;font-size:2.6px;letter-spacing:.05em;text-transform:uppercase}
.login{border:.8px solid var(--white);border-radius:6px;font-size:2.5px;padding:2px 8px}
/* platform tiles */
.tile{position:absolute;color:var(--white);display:flex;align-items:flex-end;padding:0 0 5px 6px;font-family:'Lexend Giga',sans-serif;font-size:3.2px;letter-spacing:.03em}
/* footer */
.footer h4{font-family:'Montserrat',sans-serif;font-size:3px;font-weight:600;letter-spacing:.06em;text-transform:uppercase;color:var(--navy)}
.footer ul{list-style:none;font-size:2.8px;line-height:2.6;color:var(--muted)}
.contact-row{display:flex;gap:4px;align-items:flex-start;font-size:2.8px;color:var(--muted);margin-top:3px;line-height:1.3}
.contact-row svg{flex:none}
.socials{display:flex;gap:3px;margin-top:5px}
.socials span{width:7px;height:7px;border-radius:50%;background:var(--navy);opacity:.85}
.legal{font-size:2.4px;color:var(--muted)}
.play{position:absolute}
</style>
</head>
<body>

<!-- ============ CONCEPT A : blue / teal ============ -->
<div class="page" style="left:89px;top:38px;width:317px;height:1162px">

  <section class="sec" style="height:183px;background:linear-gradient(180deg,#2b59c0 0%,#3e62ad 38%,#2a3b6c 70%,#1b2748 100%)" role="img" aria-label="Hero photograph of snow-capped mountains at dusk">
    <div class="nav" style="top:6px;padding:0 26px">
      <div class="brand"><span class="brand-dot"></span><span>VERIDIA<br><span style="font-weight:400">REAL ESTATE</span></span></div>
      <div class="nav-links" style="margin-left:34px;gap:7px"><span>About us ▾</span><span>Our businesses ▾</span><span>Investors lobby</span><span>News</span><span>Contact us</span></div>
      <div class="login" style="margin-left:12px;border-radius:0">Log in</div>
    </div>
    <div class="abs eyebrow" style="left:27px;top:64px;color:#dfe6f5">Veridia Real Estate</div>
    <div class="abs heading" style="left:27px;top:70px;font-size:10px;color:var(--white);line-height:1.05">Leading global<br>private equity<br>real estate</div>
    <div class="abs btn btn-outline" style="left:29px;top:109px;width:41px;height:10px;color:var(--white)">About us</div>
    <svg class="play" style="left:205px;top:101px" width="23" height="23" viewBox="0 0 23 23"><circle cx="11.5" cy="11.5" r="11" fill="#fff"/><path d="M9 7l7 4.5-7 4.5z" fill="#1b2748"/></svg>
    <div class="abs center-x eyebrow" style="top:163px;color:var(--white);font-size:2.6px">Scroll down</div>
    <svg class="abs" style="left:155px;top:169px" width="6" height="4" viewBox="0 0 6 4"><path d="M.5.5L3 3 5.5.5" fill="none" stroke="#fff" stroke-width=".8"/></svg>
  </section>

  <section class="sec" style="height:163px">
    <div class="abs center-x eyebrow" style="top:33px;color:var(--royal)">Who we are</div>
    <div class="abs center-x heading" style="top:38px;font-size:8.5px">Veridia Real Estate</div>
    <div class="abs rule" style="left:152px;top:50px"></div>
    <div class="abs center-x copy" style="top:57px;padding:0 48px;font-size:4px">Lorem ipsum dolor sit amet, consectetur adipiscing elit, sed do eiusmod tempor incididunt ut labore et doloreUt enim ad minim veniam, quis nostrud exercitation ullamcoea Lorem ipsum dolor sit amet, consectetur adipiscingLorem ipsum dolor sit.</div>
    <div class="abs" style="left:36px;top:97px;display:flex;gap:0">
      <div style="width:62px;text-align:left;padding-left:2px"><div class="stat-num" style="color:var(--teal)">$250</div><div class="stat-label">Real estate projects</div></div>
      <div style="width:1px;height:14px;background:#bbb;margin-top:4px"></div>
      <div style="width:66px;padding-left:12px"><div class="stat-num" style="color:var(--teal)">$25B</div><div class="stat-label">Private equity</div></div>
      <div style="width:1px;height:14px;background:#bbb;margin-top:4px"></div>
      <div style="width:66px;padding-left:14px"><div class="stat-num" style="color:var(--teal)">$13B</div><div class="stat-label">Fund solutions</div></div>
      <div style="width:1px;height:14px;background:#bbb;margin-top:4px"></div>
      <div style="width:70px;padding-left:16px"><div class="stat-num" style="color:var(--teal)">$120B</div><div class="stat-label">Credit &amp; insurance</div></div>
    </div>
    <div class="abs" style="left:160px;top:147px;width:.8px;height:16px;background:#999"></div>
  </section>

  <section class="sec" style="height:199px;background:linear-gradient(160deg,#2d9a6e 0%,#2a8a74 40%,#23516e 75%,#1f3f68 100%)">
    <div class="abs center-x eyebrow" style="top:17px;color:#e6f4ec;font-size:2.8px">Services platform</div>
    <div class="abs center-x heading" style="top:22px;font-size:8.5px;color:var(--white)">Our investment<br>platforms</div>
    <div class="tile" style="left:31px;top:51px;width:83px;height:58px;background:linear-gradient(160deg,#8fa3c4,#394a6b)" role="img" aria-label="Glass office towers from below">Lorem ipsum dolor sit</div>
    <div class="abs" style="left:118px;top:51px;width:83px;height:58px;background:#1d2f5e;border:.8px solid #9fb4dd;color:var(--white);text-align:center;padding-top:15px">
      <div style="font-size:3px;letter-spacing:.06em">SED PERSPICIATI</div>
      <div class="heading" style="font-size:3.8px;margin-top:1px">Lorem ipsum dolor sit</div>
      <div style="font-size:2.4px;line-height:1.5;margin:2px 8px 0;opacity:.85">Lorem ipsum dolor sit amet, consectetur adipiscing elit sed do eiusmod tempor</div>
      <div class="btn btn-outline" style="width:33px;height:7px;margin:4px auto 0;font-size:2.2px">Learn more</div>
    </div>
    <div class="tile" style="left:204px;top:51px;width:83px;height:58px;background:linear-gradient(150deg,#d7dde6,#2d333d 60%,#4a5563)" role="img" aria-label="Dark glass skyscrapers">Lorem ipsum dolor sit</div>
    <div class="tile" style="left:74px;top:113px;width:83px;height:57px;background:linear-gradient(160deg,#3a2f4a,#7c4f7a 45%,#201c2c)" role="img" aria-label="City towers lit at night">Lorem ipsum dolor sit</div>
    <div class="tile" style="left:160px;top:113px;width:83px;height:57px;background:linear-gradient(160deg,#cfe0f2,#7fa2c9 50%,#35557e)" role="img" aria-label="Glass tower against a cloudy sky">Lorem ipsum dolor sit</div>
  </section>

  <section class="sec" style="height:144px">
    <div class="photo" style="left:34px;top:18px;width:119px;height:105px;clip-path:polygon(25% 0,75% 0,100% 50%,75% 100%,25% 100%,0 50%);background:linear-gradient(135deg,#e8ebee,#7d8790 45%,#2a3037 75%,#aab2ba)" role="img" aria-label="Twin glass skyscrapers in black and white"></div>
    <svg class="abs" style="left:32px;top:16px" width="123" height="109" viewBox="0 0 123 109"><polygon points="31,1 92,1 122,54.5 92,108 31,108 1,54.5" fill="none" stroke="#2f9d72" stroke-width=".8"/></svg>
    <div class="abs heading" style="left:170px;top:32px;font-size:8px">Our edge</div>
    <div class="abs rule" style="left:170px;top:43px"></div>
    <div class="abs copy" style="left:170px;top:49px;width:122px"><p>Lorem ipsum dolor sit amet, consectetur adipiscing elit, sed do eiusmod tempor incididunt ut co laboris nisi ut aliquip ex ea commodo consequat.</p><p>Aabor et dolore magna aliqua. Ut enim ad minim veniam, quis nostrud exercitation ullamco laboris et dolore</p></div>
    <div class="abs btn" style="left:170px;top:96px;width:69px;height:13px;background:var(--teal);color:var(--white)">Investor information</div>
  </section>

  <section class="sec" style="height:101px;background:linear-gradient(180deg,#274f9a,#1d3f82)" role="img" aria-label="Faded city skyline in blue">
    <div class="abs center-x heading" style="top:28px;font-size:7.5px;color:var(--white)">Stay updated</div>
    <div class="abs center-x" style="top:41px;font-size:3.4px;color:#e4eaf6">Get our latest insights, firm announcements and Charitable Foundation updates.</div>
    <div class="abs field" style="left:53px;top:55px;width:80px;height:13px">NAME*</div>
    <div class="abs field" style="left:136px;top:55px;width:80px;height:13px">EMAIL*</div>
    <div class="abs btn" style="left:219px;top:55px;width:52px;height:13px;background:var(--teal);color:var(--white);font-size:3.2px">Subscribe</div>
  </section>

  <section class="sec" style="height:149px">
    <div class="abs heading" style="left:32px;top:30px;font-size:7.5px">Our responsibility</div>
    <div class="abs rule" style="left:32px;top:41px"></div>
    <div class="abs copy" style="left:32px;top:47px;width:122px"><p>Lorem ipsum dolor sit amet, consectetur adipiscing elit, sed do eiusmod tempor incididunt ut co laboris nisi ut aliquip ex ea commodo consequat.</p><p>Aabor et dolore magna aliqua. Ut enim ad minim veniam, quis nostrud exercitation ullamco laboris et dolore</p></div>
    <div class="abs btn" style="left:31px;top:94px;width:69px;height:13px;background:var(--teal);color:var(--white)">Investor information</div>
    <div class="photo" style="left:158px;top:0;width:159px;height:149px;background:linear-gradient(150deg,#c9d6e2,#7d97ad 40%,#e7e2da 70%,#5d7387)" role="img" aria-label="Colleagues working together at a meeting table"></div>
  </section>

  <section class="sec" style="height:138px;background:linear-gradient(150deg,#2b9a6a 0%,#257c6c 40%,#1b4c70 80%,#163c6c 100%)" role="img" aria-label="Mountain texture tinted teal">
    <div class="abs eyebrow" style="left:34px;top:32px;color:#e6f4ec;font-size:2.8px">Contact us</div>
    <div class="abs heading" style="left:34px;top:38px;font-size:8px;color:var(--white)">Get in touch<br>with us</div>
    <div class="abs" style="left:131px;top:32px;width:68px;border-bottom:.6px solid #cfe3dc;font-size:2.8px;color:#dbeae4;padding-bottom:3px">⌂ First Name</div>
    <div class="abs" style="left:207px;top:32px;width:68px;border-bottom:.6px solid #cfe3dc;font-size:2.8px;color:#dbeae4;padding-bottom:3px">⌂ Last Name</div>
    <div class="abs" style="left:131px;top:47px;width:68px;border-bottom:.6px solid #cfe3dc;font-size:2.8px;color:#dbeae4;padding-bottom:3px">✆ Phone Number</div>
    <div class="abs" style="left:207px;top:47px;width:68px;border-bottom:.6px solid #cfe3dc;font-size:2.8px;color:#dbeae4;padding-bottom:3px">✉ Email address</div>
    <div class="abs" style="left:131px;top:64px;width:144px;height:21px;border-bottom:.6px solid #cfe3dc;font-size:2.8px;color:#dbeae4">Message</div>
    <div class="abs btn" style="left:131px;top:93px;width:55px;height:13px;background:var(--teal);color:var(--white)">Submit message</div>
  </section>

  <section class="sec footer" style="height:83px">
    <div class="abs" style="left:35px;top:15px"><h4>Important links</h4><ul style="margin-top:3px"><li>About Us</li><li>Our Businesses</li><li>Investor Lobby</li><li>News</li><li>Contact Us</li></ul></div>
    <div class="abs" style="left:86px;top:15px;width:.5px;height:48px;background:#ccc"></div>
    <div class="abs" style="left:101px;top:15px"><h4>Explore Veridia Real Estate</h4>
      <div style="display:flex;gap:20px;margin-top:3px"><ul><li>Private Equity</li><li>Real Estate</li><li>Credit</li><li>Strategic Partners</li><li>Tactical Opportunities</li><li>Infrastructure</li></ul><ul><li>Insurance Solutions</li><li>Life Sciences</li><li>Portfolio Operations</li><li>Technology and Innovations</li><li>Registered Products</li></ul></div></div>
    <div class="abs" style="left:212px;top:15px;width:.5px;height:48px;background:#ccc"></div>
    <div class="abs" style="left:226px;top:15px"><h4>Contact details</h4>
      <div class="contact-row"><svg width="6" height="6" viewBox="0 0 10 10"><circle cx="5" cy="5" r="5" fill="#13306e"/><path d="M5 2.2a1.8 1.8 0 011.8 1.8C6.8 5.4 5 7.6 5 7.6S3.2 5.4 3.2 4A1.8 1.8 0 015 2.2z" fill="#fff"/></svg><span>82 Harbor Crest Rd Suite 4<br>Bayview, FL 33990</span></div>
      <div class="contact-row"><svg width="6" height="6" viewBox="0 0 10 10"><circle cx="5" cy="5" r="5" fill="#13306e"/><path d="M3.4 2.6l1 1.1-.5.8a4 4 0 001.6 1.6l.8-.5 1.1 1-.6.9c-2 0-4-2-4-4z" fill="#fff"/></svg><span style="color:var(--navy);font-weight:600">555-210-4786</span></div>
      <div class="contact-row"><svg width="6" height="6" viewBox="0 0 10 10"><circle cx="5" cy="5" r="5" fill="#13306e"/><rect x="2.7" y="3.4" width="4.6" height="3.2" fill="none" stroke="#fff" stroke-width=".6"/><path d="M2.7 3.4L5 5.2l2.3-1.8" fill="none" stroke="#fff" stroke-width=".6"/></svg><span style="color:var(--navy)">hello@veridiarealty.com</span></div>
      <div class="socials"><span></span><span></span><span></span><span></span></div>
    </div>
  </section>
</div>

<!-- ============ CONCEPT B : royal blue ============ -->
<div class="page" style="left:450px;top:40px;width:316px;height:1051px">

  <section class="sec" style="height:186px;background:linear-gradient(180deg,#2a2a33 0%,#4b4640 35%,#6a5a46 60%,#2c2e36 100%)" role="img" aria-label="Aerial view of city towers at night">
    <div class="nav" style="top:0;height:22px;padding:0 26px;background:rgba(30,30,38,.55)">
      <div class="brand"><span class="brand-dot"></span><span>VERIDIA<br><span style="font-weight:400">REAL ESTATE</span></span></div>
      <div class="nav-links" style="margin-left:18px;gap:8px"><span>About us ▾</span><span>Our businesses ▾</span><span>Investors lobby</span><span>News</span><span>Contact us</span></div>
      <div class="login" style="margin-left:10px">Log in</div>
    </div>
    <svg class="play" style="left:151px;top:67px" width="13" height="13" viewBox="0 0 13 13"><circle cx="6.5" cy="6.5" r="6" fill="none" stroke="#fff" stroke-width=".8"/><path d="M5 4l4 2.5L5 9z" fill="#fff"/></svg>
    <div class="abs center-x heading" style="top:84px;font-size:10px;color:var(--white)">Leading global private<br>equity real estate</div>
    <div class="abs btn btn-outline" style="left:133px;top:109px;width:50px;height:12px;color:var(--white)">About us</div>
  </section>

  <section class="sec" style="height:128px;background:var(--mist)">
    <div class="abs eyebrow" style="left:36px;top:24px;color:var(--royal)">Who we are</div>
    <div class="abs heading" style="left:36px;top:30px;font-size:8.5px">About Veridia<br>real estate</div>
    <div class="abs rule" style="left:36px;top:52px"></div>
    <div class="abs copy" style="left:36px;top:58px;width:118px"><p>Lorem ipsum dolor sit amet, consectetur adipiscing elit, sed do eiusmod tempor incididunt ut labore et dolore</p><p>Ut enim ad minim veniam, quis nostrud exercitation ullamco laboris nisi ut aliquip ex ea commodo consequat. Duis aute irure dolor in reprehenderi</p></div>
    <div class="abs" style="left:200px;top:19px;width:62px">
      <div class="stat-num" style="color:var(--royal)">$250</div><div class="stat-label" style="margin-top:2px">Real estate projects</div><div style="height:.6px;background:#bbb;margin:7px 0 6px"></div>
      <div class="stat-num" style="color:var(--royal)">$25B</div><div class="stat-label" style="margin-top:2px">Private equity</div><div style="height:.6px;background:#bbb;margin:7px 0 6px"></div>
      <div class="stat-num" style="color:var(--royal)">$13B</div><div class="stat-label" style="margin-top:2px">Fund solutions</div>
    </div>
  </section>

  <section class="sec" style="height:40px">
    <div class="abs center-x eyebrow" style="top:12px;color:var(--royal)">What we do</div>
    <div class="abs center-x heading" style="top:18px;font-size:8px">Our investment platforms</div>
    <div class="abs rule" style="left:152px;top:30px"></div>
  </section>

  <section class="sec" style="height:75px;background:#dfe7f3">
    <div class="tile" style="left:0;top:0;width:62px;height:75px;background:linear-gradient(160deg,#7b95c4,#3c5ea5)" role="img" aria-label="Laptop showing finance charts">Sed ut perspiciatis<br>unde omnis</div>
    <div class="abs" style="left:63px;top:0;width:63px;height:75px;background:var(--royal);color:var(--white);padding:20px 7px 0">
      <div class="heading" style="font-size:3.3px">Sed ut perspiciatis<br>unde omnis</div>
      <div style="font-size:2.4px;line-height:1.5;margin-top:2px;opacity:.85">Lorem ipsum dolor sit amet, consectetur adipiscing elit, sed do eiusmod tempor incididunt ut labore et</div>
      <div class="btn btn-outline" style="width:33px;height:7px;margin-top:4px;border-radius:4px;font-size:2.2px">Learn more</div>
    </div>
    <div class="tile" style="left:127px;top:0;width:63px;height:75px;background:linear-gradient(160deg,#b8c7e2,#5f7bb4)" role="img" aria-label="Modern office building">Vatem quia voluptas<br>sit aspernatur</div>
    <div class="tile" style="left:191px;top:0;width:63px;height:75px;background:linear-gradient(160deg,#c3d0e8,#6f89bd)" role="img" aria-label="Businessman overlooking a city">Sed ut perspiciatis<br>unde omnis</div>
    <div class="tile" style="left:255px;top:0;width:61px;height:75px;background:linear-gradient(160deg,#d2dcee,#8aa0c9)" role="img" aria-label="City skyline">Nemo enim ipsam<br>voluptatem</div>
  </section>

  <section class="sec" style="height:143px">
    <div class="abs heading" style="left:30px;top:30px;font-size:8px">Our edge</div>
    <div class="abs rule" style="left:30px;top:41px"></div>
    <div class="abs copy" style="left:30px;top:46px;width:120px"><p>Lorem ipsum dolor sit amet, consectetur adipiscing elit, sed do eiusmod tempor incididunt ut co laboris nisi ut aliquip ex ea commodo consequat. Duis aute irure dolor in reprehende</p><p>Aabor et dolore magna aliqua. Ut enim ad minim veniam, quis nostrud exercitation ullamco laboris nisi ut aliquip ex ea commodo consequat. Duis aute irure dolor in reprehenderitd exercitation</p></div>
    <div class="abs btn" style="left:30px;top:100px;width:72px;height:13px;background:var(--royal);color:var(--white)">Investor information</div>
    <div class="photo" style="left:145px;top:0;width:171px;height:143px;clip-path:polygon(58% 0,100% 0,100% 100%,0 100%);background:linear-gradient(135deg,#f3f3f3,#9a9a9a 45%,#2d2d2d 70%,#bdbdbd)" role="img" aria-label="Black and white glass skyscrapers from below"></div>
  </section>

  <section class="sec" style="height:101px;background:linear-gradient(180deg,#d6e1f6,#c8d6f1)" role="img" aria-label="Faint city skyline in pale blue">
    <div class="abs center-x heading" style="top:29px;font-size:7.5px">Stay updated</div>
    <div class="abs center-x" style="top:42px;font-size:3.4px;color:var(--ink)">Get our latest insights, firm announcements and Charitable Foundation updates.</div>
    <div class="abs field" style="left:51px;top:55px;width:81px;height:13px">NAME*</div>
    <div class="abs field" style="left:135px;top:55px;width:81px;height:13px">EMAIL*</div>
    <div class="abs btn" style="left:218px;top:55px;width:52px;height:13px;background:var(--royal);color:var(--white);font-size:3.2px">Subscribe</div>
  </section>

  <section class="sec" style="height:138px">
    <div class="photo" style="left:0;top:0;width:190px;height:138px;clip-path:polygon(0 0,66% 0,100% 100%,0 100%);background:linear-gradient(135deg,#6c6c6c,#d8d8d8 40%,#8a8a8a 70%,#3d3d3d)" role="img" aria-label="Black and white photo of a team meeting"></div>
    <div class="abs heading" style="left:183px;top:28px;font-size:7.5px">Our responsibility</div>
    <div class="abs copy" style="left:184px;top:42px;width:112px"><p>Lorem ipsum dolor sit amet, consectetur adipiscing elit, sed do eiusmod tempor incididunt ut</p><p>Aabor et dolore magna aliqua. Ut enim ad minim veniam, quis nostrud exercitation ullamco laboris nisi ut aliquip ex ea commodo consequat. Duis aute irure dolor in reprehenderitd exercitationna aliqua. Ut enim ad minim veniam.</p></div>
    <div class="abs btn btn-outline" style="left:184px;top:91px;width:44px;height:11px;color:var(--royal)">Learn more</div>
  </section>

  <section class="sec" style="height:137px;background:linear-gradient(110deg,#0a2a6b 0%,#0d3694 55%,#2358c4 100%)" role="img" aria-label="Blue glass architecture texture">
    <div class="abs eyebrow" style="left:32px;top:24px;color:#d7e0f5;font-size:2.8px">Contact us</div>
    <div class="abs heading" style="left:32px;top:29px;font-size:8px;color:var(--white)">Get in touch</div>
    <div class="abs field" style="left:31px;top:45px;width:61px;height:10px;background:transparent;border:.6px solid #8aa3d8;color:#cfdaf2">First Name</div>
    <div class="abs field" style="left:95px;top:45px;width:62px;height:10px;background:transparent;border:.6px solid #8aa3d8;color:#cfdaf2">Last Name</div>
    <div class="abs field" style="left:31px;top:57px;width:61px;height:10px;background:transparent;border:.6px solid #8aa3d8;color:#cfdaf2">Phone Number</div>
    <div class="abs field" style="left:95px;top:57px;width:62px;height:10px;background:transparent;border:.6px solid #8aa3d8;color:#cfdaf2">Email address</div>
    <div class="abs field" style="left:31px;top:70px;width:126px;height:21px;background:transparent;border:.6px solid #8aa3d8;color:#cfdaf2;align-items:flex-start;padding-top:2px">Message</div>
    <div class="abs btn btn-outline" style="left:31px;top:95px;width:56px;height:11px;color:var(--white)">Submit message</div>
  </section>

  <section class="sec footer" style="height:102px">
    <div class="abs" style="left:31px;top:16px"><h4>Important links</h4><ul style="margin-top:3px"><li>About Us</li><li>Our Businesses</li><li>Investor Lobby</li><li>News</li><li>Contact Us</li></ul></div>
    <div class="abs" style="left:82px;top:16px;width:.5px;height:50px;background:#ccc"></div>
    <div class="abs" style="left:92px;top:16px"><h4>Explore Veridia Real Estate</h4>
      <div style="display:flex;gap:22px;margin-top:3px"><ul><li>Private Equity</li><li>Real Estate</li><li>Credit</li><li>Strategic Partners</li><li>Tactical Opportunities</li><li>Infrastructure</li></ul><ul><li>Insurance Solutions</li><li>Life Sciences</li><li>Portfolio Operations</li><li>Technology and Innovations</li><li>Registered Products</li></ul></div></div>
    <div class="abs" style="left:206px;top:16px;width:.5px;height:50px;background:#ccc"></div>
    <div class="abs" style="left:222px;top:16px"><h4>Contact details</h4>
      <div class="contact-row"><svg width="6" height="6" viewBox="0 0 10 10"><circle cx="5" cy="5" r="5" fill="#13306e"/><path d="M5 2.2a1.8 1.8 0 011.8 1.8C6.8 5.4 5 7.6 5 7.6S3.2 5.4 3.2 4A1.8 1.8 0 015 2.2z" fill="#fff"/></svg><span>82 Harbor Crest Rd Suite 4<br>Bayview, FL 33990</span></div>
      <div class="contact-row"><svg width="6" height="6" viewBox="0 0 10 10"><circle cx="5" cy="5" r="5" fill="#13306e"/><path d="M3.4 2.6l1 1.1-.5.8a4 4 0 001.6 1.6l.8-.5 1.1 1-.6.9c-2 0-4-2-4-4z" fill="#fff"/></svg><span style="color:var(--navy);font-weight:600">555-210-4786</span></div>
      <div class="contact-row"><svg width="6" height="6" viewBox="0 0 10 10"><circle cx="5" cy="5" r="5" fill="#13306e"/><rect x="2.7" y="3.4" width="4.6" height="3.2" fill="none" stroke="#fff" stroke-width=".6"/><path d="M2.7 3.4L5 5.2l2.3-1.8" fill="none" stroke="#fff" stroke-width=".6"/></svg><span style="color:var(--navy)">hello@veridiarealty.com</span></div>
      <div class="socials"><span></span><span></span><span></span><span></span></div>
    </div>
    <div class="abs" style="left:0;right:0;top:82px;height:.6px;background:#ddd"></div>
    <div class="abs legal" style="left:30px;top:88px">Copyright © 2022 Veridia Realty</div>
    <div class="abs legal" style="right:28px;top:88px">Terms of Use &nbsp;|&nbsp; Sitemap &nbsp;|&nbsp; Privacy Policy</div>
  </section>
</div>

<!-- ============ CONCEPT C : green ============ -->
<div class="page" style="left:806px;top:38px;width:329px;height:1091px">

  <section class="sec" style="height:193px;background:linear-gradient(180deg,#2a4f86 0%,#4a6da0 35%,#3f5d86 60%,#1f3352 100%)" role="img" aria-label="Aerial view of a city skyline at dusk">
    <div class="nav" style="top:6px;padding:0 28px;border-bottom:.5px solid rgba(255,255,255,.35);padding-bottom:5px">
      <div class="brand"><span class="brand-dot"></span><span>VERIDIA<br><span style="font-weight:400">REAL ESTATE</span></span></div>
      <div class="nav-links" style="margin-left:20px;gap:9px"><span>About us ▾</span><span>Our businesses ▾</span><span>Investors lobby</span><span>News</span><span>Contact us</span></div>
      <div class="login" style="margin-left:12px;border-radius:0;border-color:var(--teal);background:var(--teal)">Log in</div>
    </div>
    <svg class="play" style="left:158px;top:64px" width="13" height="13" viewBox="0 0 13 13"><circle cx="6.5" cy="6.5" r="6" fill="none" stroke="#fff" stroke-width=".8"/><path d="M5 4l4 2.5L5 9z" fill="#fff"/></svg>
    <div class="abs center-x heading" style="top:82px;font-size:10px;color:var(--white)">Leading global private<br>equity real estate</div>
    <div class="abs btn btn-outline" style="left:139px;top:110px;width:50px;height:12px;color:var(--white)">About us</div>
    <div class="abs" style="left:0;right:0;top:166px;height:.5px;background:rgba(255,255,255,.45)"></div>
    <div class="abs" style="left:0;right:0;top:164px;display:flex;color:var(--white);text-align:center">
      <div style="flex:1"><div style="width:3px;height:3px;border-radius:50%;background:#fff;margin:0 auto 1px"></div><div class="stat-num" style="font-size:8px">$250</div><div class="stat-label" style="font-size:2.7px">Real estate projects</div></div>
      <div style="flex:1"><div style="width:3px;height:3px;border-radius:50%;background:#fff;margin:0 auto 1px"></div><div class="stat-num" style="font-size:8px">$25B</div><div class="stat-label" style="font-size:2.7px">Private equity</div></div>
      <div style="flex:1"><div style="width:3px;height:3px;border-radius:50%;background:#fff;margin:0 auto 1px"></div><div class="stat-num" style="font-size:8px">$13B</div><div class="stat-label" style="font-size:2.7px">Fund solutions</div></div>
      <div style="flex:1"><div style="width:3px;height:3px;border-radius:50%;background:#fff;margin:0 auto 1px"></div><div class="stat-num" style="font-size:8px">$10B</div><div class="stat-label" style="font-size:2.7px">Private equity</div></div>
    </div>
  </section>

  <section class="sec" style="height:106px">
    <div class="abs eyebrow" style="left:38px;top:27px;color:#999">Who we are</div>
    <div class="abs heading" style="left:38px;top:32px;font-size:8.5px">About Veridia<br>real estate</div>
    <div class="abs rule" style="left:38px;top:54px"></div>
    <div class="abs btn btn-outline" style="left:38px;top:64px;width:43px;height:11px;color:var(--forest)">Learn more</div>
    <div class="abs copy" style="left:151px;top:30px;width:145px;color:var(--ink)">Lorem ipsum dolor sit amet, consectetur adipiscing elit, sed do eiusmod tempor incididunt ut labore et doloreUt enim ad minim veniam, quis nostrud exercitation ullamco laboris nisi ut aliquip ex ea Lorem ipsum dolor sit amet, consectetur adipiscing elitLorem ipsum dolor sit amet, consectetur adipiscing elit sed.</div>
  </section>

  <section class="sec" style="height:139px;background:var(--mint)">
    <div class="abs center-x heading" style="top:15px;font-size:8px">Our investment platforms</div>
    <div class="abs rule" style="left:158px;top:26px"></div>
    <div class="abs" style="left:78px;top:40px;width:59px;height:79px;background:#6aa56a;border:.8px solid var(--forest)"></div>
    <div class="abs" style="left:0;right:0;top:45px;display:flex;justify-content:center;gap:4px">
      <div style="width:58px;margin-left:4px;text-align:center;color:var(--ink)">
        <svg width="26" height="26" viewBox="0 0 26 26"><circle cx="13" cy="13" r="11.5" fill="#fff" stroke="#2f7a34" stroke-width="1.6"/><rect x="8" y="14" width="2.4" height="5" fill="#2f7a34"/><rect x="12" y="11" width="2.4" height="8" fill="#2f7a34"/><rect x="16" y="8" width="2.4" height="11" fill="#2f7a34"/></svg>
        <div style="font-size:2.8px;font-weight:600;margin-top:2px">SED UT PERSPICIATIS<br>UNDE OMNIS</div>
        <div style="font-size:2.3px;line-height:1.4;color:var(--muted);margin-top:1px">Lorem ipsum dolor sit amet, consectetur adipiscing elit, sed do eiusmod</div>
        <div class="btn btn-outline" style="width:30px;height:7px;margin:4px auto 0;font-size:2.1px;color:var(--forest)">Learn more</div>
      </div>
      <div style="width:58px;text-align:center;color:var(--white)">
        <svg width="26" height="26" viewBox="0 0 26 26"><circle cx="13" cy="13" r="11.5" fill="#fff" stroke="#dff0df" stroke-width="1.6"/><rect x="8" y="9" width="10" height="9" fill="none" stroke="#2f7a34" stroke-width="1.2"/><path d="M8 12h10" stroke="#2f7a34" stroke-width="1"/></svg>
        <div style="font-size:2.8px;font-weight:600;margin-top:2px">SED UT PERSPICIATIS<br>UNDE OMNIS</div>
        <div style="font-size:2.3px;line-height:1.4;margin-top:1px;opacity:.9">Lorem ipsum dolor sit amet, consectetur adipiscing elit, sed do eiusmod</div>
        <div style="font-size:2.1px;margin-top:5px;letter-spacing:.1em">LEARN MORE</div>
      </div>
      <div style="width:58px;text-align:center;margin-left:4px">
        <svg width="26" height="26" viewBox="0 0 26 26"><circle cx="13" cy="13" r="11.5" fill="#fff" stroke="#2f7a34" stroke-width="1.6"/><path d="M7 18l4-4 3 2 5-6" fill="none" stroke="#2f7a34" stroke-width="1.3"/></svg>
        <div style="font-size:2.8px;font-weight:600;margin-top:2px">SED UT PERSPICIATIS<br>UNDE OMNIS</div>
        <div style="font-size:2.3px;line-height:1.4;color:var(--muted);margin-top:1px">Lorem ipsum dolor sit amet, consectetur adipiscing elit, sed do eiusmod</div>
        <div class="btn btn-outline" style="width:30px;height:7px;margin:4px auto 0;font-size:2.1px;color:var(--forest)">Learn more</div>
      </div>
      <div style="width:58px;text-align:center">
        <svg width="26" height="26" viewBox="0 0 26 26"><circle cx="13" cy="13" r="11.5" fill="#fff" stroke="#2f7a34" stroke-width="1.6"/><rect x="9" y="7" width="8" height="12" fill="none" stroke="#2f7a34" stroke-width="1.2"/><path d="M11 10h4M11 13h4M11 16h4" stroke="#2f7a34" stroke-width=".9"/></svg>
        <div style="font-size:2.8px;font-weight:600;margin-top:2px">SED UT PERSPICIATIS<br>UNDE OMNIS</div>
        <div style="font-size:2.3px;line-height:1.4;color:var(--muted);margin-top:1px">Lorem ipsum dolor sit amet, consectetur adipiscing elit, sed do eiusmod</div>
        <div class="btn btn-outline" style="width:30px;height:7px;margin:4px auto 0;font-size:2.1px;color:var(--forest)">Learn more</div>
      </div>
      <div style="width:58px;text-align:center">
        <svg width="26" height="26" viewBox="0 0 26 26"><circle cx="13" cy="13" r="11.5" fill="#fff" stroke="#2f7a34" stroke-width="1.6"/><rect x="7.5" y="8" width="11" height="8" fill="none" stroke="#2f7a34" stroke-width="1.2"/><path d="M11 19h4" stroke="#2f7a34" stroke-width="1.2"/></svg>
        <div style="font-size:2.8px;font-weight:600;margin-top:2px">SED UT PERSPICIATIS<br>UNDE OMNIS</div>
        <div style="font-size:2.3px;line-height:1.4;color:var(--muted);margin-top:1px">Lorem ipsum dolor sit amet, consectetur adipiscing elit, sed do eiusmod</div>
        <div class="btn btn-outline" style="width:30px;height:7px;margin:4px auto 0;font-size:2.1px;color:var(--forest)">Learn more</div>
      </div>
    </div>
  </section>

  <section class="sec" style="height:152px">
    <div class="photo" style="left:0;top:0;width:163px;height:152px;background:linear-gradient(150deg,#e4efe4,#a9cfa6 35%,#3f8c45 65%,#1f5e22)" role="img" aria-label="Green glass tower against clouds"></div>
    <div class="abs heading" style="left:184px;top:30px;font-size:8px">Our edge</div>
    <div class="abs rule" style="left:184px;top:41px"></div>
    <div class="abs copy" style="left:184px;top:47px;width:122px"><p>Lorem ipsum dolor sit amet, consectetur adipiscing elit, sed do eiusmod tempor incididunt ut co laboris nisi ut aliquip ex ea commodo consequat. Duis aute irure dolor in reprehende</p><p>Aabor et dolore magna aliqua. Ut enim ad minim veniam, quis nostrud exercitation ullamco laboris nisi ut aliquip ex ea commodo consequat. Duis aute irure dolor in reprehenderitd exercitation</p></div>
    <div class="abs btn" style="left:184px;top:106px;width:75px;height:14px;background:var(--forest-dark);color:var(--white)">Investor information</div>
  </section>

  <section class="sec" style="height:105px;background:linear-gradient(180deg,#3f8440,#2f7434)" role="img" aria-label="Faint city skyline in green">
    <div class="abs center-x heading" style="top:32px;font-size:7.5px;color:var(--white)">Stay updated</div>
    <div class="abs center-x" style="top:45px;font-size:3.4px;color:#e3f0e3">Get our latest insights, firm announcements and Charitable Foundation updates.</div>
    <div class="abs field" style="left:55px;top:57px;width:84px;height:13px">NAME*</div>
    <div class="abs field" style="left:141px;top:57px;width:84px;height:13px">EMAIL*</div>
    <div class="abs btn" style="left:227px;top:57px;width:56px;height:13px;background:var(--leaf);color:var(--white);font-size:3.2px">Subscribe</div>
  </section>

  <section class="sec" style="height:149px">
    <div class="photo" style="left:36px;top:20px;width:114px;height:114px;border-radius:50%;background:linear-gradient(135deg,#5d5d5d,#d4d4d4 45%,#8b8b8b 70%,#3a3a3a)" role="img" aria-label="Black and white photo of colleagues at a meeting"></div>
    <div class="abs heading" style="left:174px;top:37px;font-size:7.5px">Our responsibility</div>
    <div class="abs copy" style="left:175px;top:52px;width:118px"><p>Lorem ipsum dolor sit amet, consectetur adipiscing elit, sed do eiusmod tempor incididunt ut</p><p>Aabor et dolore magna aliqua. Ut enim ad minim veniam, quis nostrud exercitation ullamco laboris nisi ut aliquip ex ea commodo consequat. Duis aute irure dolor in reprehenderitd exercitationna aliqua. Ut enim ad minim veniam.</p></div>
    <div class="abs btn btn-outline" style="left:175px;top:100px;width:46px;height:11px;color:var(--forest)">Learn more</div>
  </section>

  <section class="sec" style="height:141px;background:var(--mint)">
    <div class="abs eyebrow" style="left:32px;top:23px;color:var(--muted);font-size:2.8px">Contact us</div>
    <div class="abs heading" style="left:32px;top:28px;font-size:8px">Get in touch</div>
    <div class="abs field" style="left:31px;top:43px;width:58px;height:10px">First Name</div>
    <div class="abs field" style="left:91px;top:43px;width:60px;height:10px">Last Name</div>
    <div class="abs field" style="left:31px;top:55px;width:58px;height:10px">Phone Number</div>
    <div class="abs field" style="left:91px;top:55px;width:60px;height:10px">Email address</div>
    <div class="abs field" style="left:31px;top:68px;width:120px;height:21px;align-items:flex-start;padding-top:2px">Message</div>
    <div class="abs btn" style="left:31px;top:96px;width:57px;height:11px;background:var(--forest-dark);color:var(--white)">Submit message</div>
    <div class="photo" style="left:165px;top:0;width:164px;height:141px;background:linear-gradient(140deg,#dfe6e8,#a9b8bd 40%,#6d6a62 70%,#c9cdd0)" role="img" aria-label="Team discussing documents in a bright office"></div>
  </section>

  <section class="sec footer" style="height:106px;background:var(--footer)">
    <div class="abs" style="left:34px;top:16px"><h4>Important links</h4><ul style="margin-top:3px"><li>About Us</li><li>Our Businesses</li><li>Investor Lobby</li><li>News</li><li>Contact Us</li></ul></div>
    <div class="abs" style="left:96px;top:16px"><h4>Explore Veridia Real Estate</h4>
      <div style="display:flex;gap:22px;margin-top:3px"><ul><li>Private Equity</li><li>Real Estate</li><li>Credit</li><li>Strategic Partners</li><li>Tactical Opportunities</li><li>Infrastructure</li></ul><ul><li>Insurance Solutions</li><li>Life Sciences</li><li>Portfolio Operations</li><li>Technology and Innovations</li><li>Registered Products</li></ul></div></div>
    <div class="abs" style="left:231px;top:16px"><h4>Contact details</h4>
      <div class="contact-row"><svg width="6" height="6" viewBox="0 0 10 10"><circle cx="5" cy="5" r="5" fill="#13306e"/><path d="M5 2.2a1.8 1.8 0 011.8 1.8C6.8 5.4 5 7.6 5 7.6S3.2 5.4 3.2 4A1.8 1.8 0 015 2.2z" fill="#fff"/></svg><span>82 Harbor Crest Rd Suite 4<br>Bayview, FL 33990</span></div>
      <div class="contact-row"><svg width="6" height="6" viewBox="0 0 10 10"><circle cx="5" cy="5" r="5" fill="#13306e"/><path d="M3.4 2.6l1 1.1-.5.8a4 4 0 001.6 1.6l.8-.5 1.1 1-.6.9c-2 0-4-2-4-4z" fill="#fff"/></svg><span style="color:var(--navy);font-weight:600">555-210-4786</span></div>
      <div class="contact-row"><svg width="6" height="6" viewBox="0 0 10 10"><circle cx="5" cy="5" r="5" fill="#13306e"/><rect x="2.7" y="3.4" width="4.6" height="3.2" fill="none" stroke="#fff" stroke-width=".6"/><path d="M2.7 3.4L5 5.2l2.3-1.8" fill="none" stroke="#fff" stroke-width=".6"/></svg><span style="color:var(--navy)">hello@veridiarealty.com</span></div>
      <div class="socials"><span></span><span></span><span></span><span></span></div>
    </div>
    <div class="abs" style="left:0;right:0;top:85px;height:.6px;background:#d8dadd"></div>
    <div class="abs legal" style="left:31px;top:93px">Copyright © 2022 Veridia Realty</div>
    <div class="abs legal" style="right:37px;top:93px">Terms of Use &nbsp;|&nbsp; Sitemap &nbsp;|&nbsp; Privacy Policy</div>
  </section>
</div>

</body>
</html>
```